Young company in the agrifood product sector *

Our company% 26 # 233; t% 26 # 233; Ambrel Crest low% 26 # 233; % 26 # 224; Toulouse et sp% 26 # 233; cialis% 26 # 233; in the packaging and marketing of beehive products, We need a design of% 26 # 39;% 26 # 39;% 26 # 233; label for honey jar of 250g, The% 26 # 233; labels destiny% 26 # 233; the honey jars will be transparent so that the nectar is visible from the front, our Ambrel Crest logo must be% 26 # 234; be located% 26 # 233; above / middle of% 26 # 393% label followed below the appellation, for example Ch% 26 # 226; taignier followed below the country of% 26 # 39; origin France tracking below r% 26 # 233; region of r% 26 # 233; colte Midi-Pyr% 26 # 233; n% 26 # 233; es and below l% 26 # 39;% 26 # 233; label weight 250g and% 26lt;% 26lt;% 26lt; Honey% 26gt;% 26gt; on the% 26 # 39;% 26 # 233; label will be a plus but optional, The dimensions of the% 26 # 39;% 26 # 233; label are the following 6cm x 6cm. The design must inspire quality% 26 # 233; luxury, l% 26 # 39;% 26 # 233; l% 26 # 233; elegance and confidence, these are quality honey% 26 # 233; and rare honeys from around the world which are very expensive. Very important, the honeys have different colors, this can range from white to orange yellow or darker shades of brown% 26 # 234; black, that's why we would like to have at least 3 colors for light honey, medium dark% 26 # 233; and dark% 26 # 233 ;, Regarding the colors you have free choice of course% 26 # 251; r taking into account the colors of the honey which must% 26 # 234; be visible% 26 # 224; through the% 26 # 39;% 26 # 233; transparent label You will find attached the files of our Ambrel Crest logo. 20%% 26 # 224; 40% transparency on the% 26 # 39;% 26 # 233; label would be reasonable but% 26 # 224; you to see which is better, thanks
- Krone one

```html
<!DOCTYPE html>
<html lang="fr">
<head>
<meta charset="utf-8">
<title>Ambrel Crest – Étiquettes miel 250g</title>
<link href="https://fonts.googleapis.com/css2?family=Quicksand:wght@600;700&display=swap" rel="stylesheet">
<style>
  :root {
    --canvas-bg: #eef0f1;
    --honey-light: #f6b83a;
    --honey-gold: #f2a428;
    --honey-amber: #e96a1c;
    --honey-dark: #c42410;
    --ink-black: #111111;
    --ink-white: #ffffff;
    --gold-hi: #e9cfa6;
    --gold-lo: #a88452;
    --silver-hi: #f3f0ec;
    --silver-lo: #b9b1a8;
  }
  * { margin: 0; padding: 0; box-sizing: border-box; }
  html, body {
    width: 1200px; height: 923px; overflow: hidden;
    background: var(--canvas-bg);
    font-family: "Quicksand", sans-serif;
  }
  .label-range {
    position: absolute; inset: 0;
    display: flex; justify-content: center; align-items: center; gap: 30px;
  }
  .honey-label {
    width: 250px; height: 340px; border-radius: 18px;
    overflow: hidden;
  }
  .honey-label--light { background: var(--honey-light); }
  .honey-label--gold { background: var(--honey-gold); }
  .honey-label--amber { background: var(--honey-amber); }
  .honey-label--dark { background: var(--honey-dark); }
  .honey-label svg { display: block; width: 250px; height: 340px; }
  .brand-name { font-weight: 700; font-size: 20px; }
  .variety { font-weight: 700; font-size: 27px; letter-spacing: 0.5px; }
  .origin { font-weight: 700; font-size: 19px; letter-spacing: 2px; }
  .region { font-weight: 700; font-size: 10px; }
  .weight { font-weight: 700; font-size: 12px; }
</style>
</head>
<body>
<main class="label-range">

  <!-- Light honey: black print -->
  <section class="honey-label honey-label--light">
    <svg viewBox="0 0 250 340">
      <g fill="var(--ink-black)">
        <circle cx="56" cy="40" r="8"/>
        <text class="brand-name" x="135" y="47" text-anchor="middle">Ambrel Crest</text>
        <path d="M18,150 L18,125 Q18,98 60,96 L190,96 Q232,98 232,125 L232,150 Z"/>
        <path d="M35,168 L215,168 L200,200 Q195,206 185,206 L65,206 Q55,206 50,200 Z"/>
        <path d="M68,222 L182,222 L170,244 L80,244 Z"/>
        <path d="M100,262 L150,262 L125,290 Z"/>
        <text class="weight" x="125" y="315" text-anchor="middle">250g</text>
      </g>
      <g fill="var(--honey-light)" text-anchor="middle">
        <text class="variety" x="125" y="133">Châtaignier</text>
        <text class="origin" x="125" y="194">FRANCE</text>
        <text class="region" x="125" y="237">Midi-Pyrénées</text>
      </g>
    </svg>
  </section>

  <!-- Golden honey: gold foil print -->
  <section class="honey-label honey-label--gold">
    <svg viewBox="0 0 250 340">
      <defs>
        <linearGradient id="foil-gold" x1="0" y1="0" x2="1" y2="0">
          <stop offset="0" stop-color="var(--gold-lo)"/>
          <stop offset="0.5" stop-color="var(--gold-hi)"/>
          <stop offset="1" stop-color="var(--gold-lo)"/>
        </linearGradient>
      </defs>
      <g fill="url(#foil-gold)">
        <circle cx="56" cy="40" r="8"/>
        <text class="brand-name" x="135" y="47" text-anchor="middle">Ambrel Crest</text>
        <path d="M18,150 L18,125 Q18,98 60,96 L190,96 Q232,98 232,125 L232,150 Z"/>
        <path d="M35,168 L215,168 L200,200 Q195,206 185,206 L65,206 Q55,206 50,200 Z"/>
        <path d="M68,222 L182,222 L170,244 L80,244 Z"/>
        <path d="M100,262 L150,262 L125,290 Z"/>
        <text class="weight" x="125" y="315" text-anchor="middle">250g</text>
      </g>
      <g fill="var(--honey-gold)" text-anchor="middle">
        <text class="variety" x="125" y="133">Châtaignier</text>
        <text class="origin" x="125" y="194">FRANCE</text>
        <text class="region" x="125" y="237">Midi-Pyrénées</text>
      </g>
    </svg>
  </section>

  <!-- Amber honey: silver foil print -->
  <section class="honey-label honey-label--amber">
    <svg viewBox="0 0 250 340">
      <defs>
        <linearGradient id="foil-silver" x1="0" y1="0" x2="1" y2="0">
          <stop offset="0" stop-color="var(--silver-lo)"/>
          <stop offset="0.5" stop-color="var(--silver-hi)"/>
          <stop offset="1" stop-color="var(--silver-lo)"/>
        </linearGradient>
      </defs>
      <g fill="var(--ink-white)">
        <circle cx="56" cy="40" r="8"/>
        <text class="brand-name" x="135" y="47" text-anchor="middle">Ambrel Crest</text>
        <text class="weight" x="125" y="315" text-anchor="middle">250g</text>
      </g>
      <g fill="url(#foil-silver)">
        <path d="M18,150 L18,125 Q18,98 60,96 L190,96 Q232,98 232,125 L232,150 Z"/>
        <path d="M35,168 L215,168 L200,200 Q195,206 185,206 L65,206 Q55,206 50,200 Z"/>
        <path d="M68,222 L182,222 L170,244 L80,244 Z"/>
        <path d="M100,262 L150,262 L125,290 Z"/>
      </g>
      <g fill="var(--honey-amber)" text-anchor="middle">
        <text class="variety" x="125" y="133">Châtaignier</text>
        <text class="origin" x="125" y="194">FRANCE</text>
        <text class="region" x="125" y="237">Midi-Pyrénées</text>
      </g>
    </svg>
  </section>

  <!-- Dark honey: white print -->
  <section class="honey-label honey-label--dark">
    <svg viewBox="0 0 250 340">
      <g fill="var(--ink-white)">
        <circle cx="56" cy="40" r="8"/>
        <text class="brand-name" x="135" y="47" text-anchor="middle">Ambrel Crest</text>
        <path d="M18,150 L18,125 Q18,98 60,96 L190,96 Q232,98 232,125 L232,150 Z"/>
        <path d="M35,168 L215,168 L200,200 Q195,206 185,206 L65,206 Q55,206 50,200 Z"/>
        <path d="M68,222 L182,222 L170,244 L80,244 Z"/>
        <path d="M100,262 L150,262 L125,290 Z"/>
        <text class="weight" x="125" y="315" text-anchor="middle">250g</text>
      </g>
      <g fill="var(--honey-dark)" text-anchor="middle">
        <text class="variety" x="125" y="133">Châtaignier</text>
        <text class="origin" x="125" y="194">FRANCE</text>
        <text class="region" x="125" y="237">Midi-Pyrénées</text>
      </g>
    </svg>
  </section>

</main>
</body>
</html>
```